Double-sided A5 leaflet with photos.

Design A5 leaflet double sided
With emphasis on we are cheaper than our competition as a hook
The colour can be whatever makes it look like a unique brand.
Try and use all the different photos because they are unique.
And put the different photos on there with headlines
Updates

Need extra days to review

Target Market(s)

The idea is it stands out people moving that you can offer different things to like taking their bed apart, taking their old furniture or they just want to move and want two men and the truck. Big or small or piano? Heavy furniture marble table? People who want their bed taken apart put back together again, piano moving, marble table. Moving fridge for washing machine. Moving small truck picture of big truck the poster is people walking past in the street. The pelmo leaflet is delivered to high rise unit blocks with 300 units.

Industry/Entity Type

Furniture removal

Colors
59FF00
82FF00
B8FF75
E3FFCB
F4FFEA

Requirements
Must have
• Try and use all the different photos the screenshot of the Varnex review next to the other photos we put beds together, etc
Nice to have
• It would be nice to have on one side all the different photos with headlines on each one saying what they do EG beds taken apart over the top of a photo .g

```html
<!DOCTYPE html>
<html lang="en">
<head>
<meta charset="utf-8">
<title>Steady Movers – A5 Leaflet</title>
<link href="https://fonts.googleapis.com/css2?family=Roboto+Condensed:wght@400;700;900&family=Oswald:wght@400;500;600&family=Roboto+Slab:wght@800;900&family=Open+Sans:wght@600&display=swap" rel="stylesheet">
<style>
  :root{
    --bg:#e4e4e4;
    --green-deep:#0b6b2e;
    --green-mid:#2f9a1f;
    --green-bright:#59b81c;
    --green-lime:#8fd22a;
    --yellow:#f3f01a;
    --yellow-warm:#f7c51a;
    --red:#e3101b;
    --white:#ffffff;
    --ink:#4a4a4a;
    --rule:#c9c9c9;
  }
  *{box-sizing:border-box;margin:0;padding:0}
  html,body{width:1200px;height:1152px;overflow:hidden;background:var(--bg)}
  .canvas{position:relative;width:1200px;height:1152px}
  .card{position:absolute;left:80px;width:1040px;height:500px;overflow:hidden;box-shadow:0 6px 14px rgba(0,0,0,.35)}
  .card--front{top:48px;background:linear-gradient(180deg,var(--green-bright),var(--green-lime) 60%,var(--green-bright))}
  .card--back{top:604px;background:var(--white)}

  /* front */
  .front__flare{position:absolute;inset:0;background:linear-gradient(125deg,var(--yellow-warm) 0%,rgba(247,197,26,.6) 14%,rgba(89,184,28,0) 32%)}
  .front__topline{position:absolute;left:0;right:0;top:0;height:8px;background:linear-gradient(90deg,var(--yellow-warm),var(--yellow))}
  .headline{position:absolute;right:24px;top:14px;font-family:"Roboto Condensed",sans-serif;font-weight:900;font-size:92px;letter-spacing:-1px;color:var(--white);text-shadow:3px 4px 4px rgba(0,60,0,.55)}
  .rule-yellow{position:absolute;left:300px;right:0;height:6px;background:linear-gradient(90deg,rgba(243,240,26,0),var(--yellow-warm) 30%,var(--yellow))}
  .rule-yellow--top{top:132px}
  .rule-yellow--bottom{top:306px}
  .rate-band{position:absolute;left:0;right:0;top:144px;height:156px;background:var(--green-deep)}
  .rate-band__price{position:absolute;left:400px;top:4px;font-family:"Oswald",sans-serif;font-weight:500;font-size:124px;line-height:1;color:var(--yellow)}
  .rate-band__unit{position:absolute;left:735px;top:18px;font-family:"Oswald",sans-serif;font-size:52px;color:var(--white)}
  .rate-band__note{position:absolute;left:650px;top:86px;font-family:"Oswald",sans-serif;font-size:41px;color:var(--white)}
  .brand-badge{position:absolute;left:34px;top:70px;width:370px;height:370px;border-radius:50%;background:var(--green-deep);border:8px solid var(--white);display:flex;align-items:center;justify-content:center;box-shadow:0 4px 12px rgba(0,0,0,.35)}
  .brand-badge__name{font-family:"Roboto Condensed",sans-serif;font-weight:900;font-size:54px;line-height:1;color:var(--white);text-align:center}
  .compare{position:absolute;top:324px;height:166px;display:flex;align-items:center;gap:22px}
  .compare--duo{left:440px;width:270px}
  .compare--van{left:736px;width:290px}
  .compare__divider{position:absolute;left:720px;top:324px;width:4px;height:176px;background:var(--white)}
  .compare__name{font-family:"Roboto Condensed",sans-serif;font-weight:700;font-size:34px;line-height:.95;color:var(--ink);letter-spacing:-1px}
  .compare__dot{width:92px;height:92px;border-radius:50%;background:var(--green-deep);flex:none}
  .compare__prices{font-family:"Oswald",sans-serif;font-size:26px;line-height:1.05;color:var(--ink);text-align:center}
  .compare__prices .price{color:var(--red);font-weight:600}
  .compare__prices .price--lead{font-size:36px}

  /* back */
  .back__panel{position:absolute;left:0;top:0;width:590px;height:500px;background:linear-gradient(180deg,var(--green-lime),var(--green-bright))}
  .back__topline{position:absolute;left:0;width:590px;top:0;height:8px;background:linear-gradient(90deg,var(--yellow-warm),var(--yellow))}
  .back__corner{position:absolute;right:0;top:0;width:160px;height:130px;background:linear-gradient(215deg,var(--green-deep) 40%,rgba(11,107,46,0) 70%)}
  .back__headline{position:absolute;left:0;width:590px;top:14px;text-align:center;font-family:"Roboto Slab",serif;font-weight:900;font-size:50px;line-height:1.02;color:#eef8c6;text-shadow:2px 3px 3px rgba(0,60,0,.5)}
  .back__photo{position:absolute;left:0;top:126px;width:590px;height:250px;background:linear-gradient(120deg,#9fb6d4 0%,#e8ecef 30%,#6f8f5a 60%,#24301f 85%)}
  .back__phone{position:absolute;left:0;width:590px;top:370px;text-align:center;font-family:"Roboto Slab",serif;font-weight:900;font-size:64px;color:var(--yellow);text-shadow:2px 3px 3px rgba(0,60,0,.5)}
  .back__web{position:absolute;left:0;width:590px;top:452px;text-align:center;font-family:"Roboto Slab",serif;font-weight:800;font-size:26px;color:#eef8c6}
  .postal{position:absolute;left:590px;top:0;width:450px;height:500px}
  .postal__line{position:absolute;left:20px;right:20px;height:2px;background:var(--rule)}
</style>
</head>
<body>
<main class="canvas">

  <section class="card card--front" aria-label="Leaflet front">
    <div class="front__flare"></div>
    <div class="front__topline"></div>
    <h1 class="headline">Compare Quotos</h1>
    <div class="rule-yellow rule-yellow--top"></div>
    <div class="rate-band">
      <span class="rate-band__price">$170</span>
      <span class="rate-band__unit">per hour</span>
      <span class="rate-band__note">No base to base Charge</span>
    </div>
    <div class="rule-yellow rule-yellow--bottom"></div>

    <div class="brand-badge"><span class="brand-badge__name">STEADY<br>MOVERS</span></div>

    <div class="compare compare--duo">
      <span class="compare__name">DUO<br>HAULERS</span>
      <p class="compare__prices">Ist hour<br><span class="price">$ 465</span><br>then<br><span class="price">$ 250</span><br>per hour</p>
    </div>
    <div class="compare__divider"></div>
    <div class="compare compare--van">
      <span class="compare__dot"></span>
      <span class="compare__name" style="display:none"></span>
      <p class="compare__prices"><span class="compare__name">VAN CREW</span><br><span class="price price--lead">$ 225</span><br>per hour<br>base to base<br>from Northvale</p>
    </div>
  </section>

  <section class="card card--back" aria-label="Leaflet back">
    <div class="back__panel"></div>
    <div class="back__corner"></div>
    <div class="back__topline"></div>
    <h2 class="back__headline">VERY VERY VERY<br>CHEAP MOVERS</h2>
    <div class="back__photo" role="img" aria-label="Photo of the moving truck and a mover wheeling a strapped upright piano"></div>
    <p class="back__phone">0400 123 456</p>
    <p class="back__web">www.steadymovers.com.au</p>

    <div class="postal">
      <svg width="450" height="200" viewBox="0 0 450 200" aria-hidden="true">
        <circle cx="115" cy="100" r="62" fill="none" stroke="#555" stroke-width="2"/>
        <g fill="none" stroke="#555" stroke-width="2">
          <path d="M170 82 q10 -8 20 0 t20 0 t20 0 t20 0 t20 0"/>
          <path d="M170 94 q10 -8 20 0 t20 0 t20 0 t20 0 t20 0"/>
          <path d="M170 106 q10 -8 20 0 t20 0 t20 0 t20 0 t20 0"/>
          <path d="M170 118 q10 -8 20 0 t20 0 t20 0 t20 0 t20 0"/>
        </g>
        <rect x="300" y="26" width="126" height="160" fill="none" stroke="#555" stroke-width="3" stroke-dasharray="4 4"/>
        <rect x="306" y="32" width="114" height="148" fill="#fff" stroke="#555" stroke-width="1.5"/>
      </svg>
      <div class="postal__line" style="top:250px"></div>
      <div class="postal__line" style="top:310px"></div>
      <div class="postal__line" style="top:370px"></div>
      <div class="postal__line" style="top:430px"></div>
    </div>
  </section>

</main>
</body>
</html>
```